4th Generation Family Business Needs a New Card Design!

We are a family owned 4th Generation company. We are based in the Sydney, Australia area and we are desperately in need of a more modern and classy card. We are monumental masons who design, supply & erect lasting memorials throughout cemeteries in Sydney. Our customers are normally in a period of grieving. I have attached logo files that will need to be implemented on the card. Company was established 1935. Australian Owned and Operated. Card needs to be designed to PIXO.com specification.

Target Market(s)

Our target market is based upon people that a grieving for family members that have passed away. We also deal with alot of companies that own and operate cemeteries.

Industry/Entity Type

Business

Contact Information for Business Card

Simon Harcourt, Operations Manager, 0417293086, simon@harcourtmemorials.com.au
Lewis Harcourt, Director, 0491630572, lewis@harcourtmemorials.com.au
Phone # 02 9561 3048
Website: www.harcourtmemorials.com.au
Address: Suite 17, 8 Palfrey Lane, West Carlow, Sydney NSW 2156

Font styles to use
Serif
Decorative
Script

Requirements
Must have
• Would like to see the logo nicely implemented with a modern design. Embossed lettering would be a nice additive.

```html
<!DOCTYPE html>
<html lang="en">
<head>
<meta charset="utf-8">
<title>Harcourt Memorials – Business Card</title>
<link href="https://fonts.googleapis.com/css2?family=Cinzel:wght@400;600&family=Noticia+Text&display=swap" rel="stylesheet">
<style>
  :root {
    --page: #e6e6e6;
    --card: #f9f9f8;
    --ink: #1a1a1a;
    --black: #0d0d0d;
    --gold: #e9b70f;
    --gold-deep: #c99a08;
    --white-text: #f2f2f2;
  }
  * { margin: 0; padding: 0; box-sizing: border-box; }
  html, body { width: 1200px; height: 576px; overflow: hidden; }
  body { background: var(--page); position: relative; font-family: "Noticia Text", Georgia, serif; }

  .card {
    position: absolute;
    background: var(--card);
    box-shadow: 0 2px 4px rgba(0,0,0,.25);
    overflow: hidden;
  }
  .card--front { left: 80px; top: 138px; width: 486px; height: 294px; }
  .card--back { left: 602px; top: 138px; width: 481px; height: 291px; }

  .front-band {
    position: absolute; left: 0; right: 0; bottom: 0; height: 10px;
    background: linear-gradient(180deg, var(--gold), var(--gold-deep));
  }

  .wordmark {
    position: absolute;
    display: flex; flex-direction: column; align-items: center;
    font-family: "Cinzel", "Times New Roman", serif;
    font-weight: 600;
    color: var(--ink);
    line-height: 1;
    text-align: center;
  }
  .wordmark__mark {
    width: 44px; height: 44px; border: 3px solid var(--ink); margin-bottom: 14px;
  }
  .wordmark__name { font-size: 34px; letter-spacing: 1px; }
  .wordmark__sub { font-size: 17px; letter-spacing: 2px; margin-top: 6px; }
  .card--front .wordmark { left: 0; right: 0; top: 84px; }
  .card--back .wordmark { left: 268px; width: 210px; top: 84px; }
  .card--back .wordmark__name { font-size: 28px; }
  .card--back .wordmark__sub { font-size: 14px; }

  .back-art { position: absolute; inset: 0; }

  .person { position: absolute; left: 24px; top: 22px; }
  .person__name {
    font-family: "Cinzel", "Times New Roman", serif;
    font-weight: 600; font-size: 21px; letter-spacing: .5px;
    color: var(--gold);
  }
  .person__role { font-size: 11px; color: var(--white-text); margin-top: 3px; }

  .contact { position: absolute; left: 24px; top: 160px; color: var(--white-text); font-size: 12px; }
  .contact__address { line-height: 18px; margin-bottom: 5px; }
  .contact__list { list-style: none; }
  .contact__item { display: flex; align-items: center; height: 17px; line-height: 17px; }
  .contact__icon { width: 10px; height: 10px; margin-right: 12px; flex: none; }
</style>
</head>
<body>

<section class="card card--front" aria-label="Card front">
  <div class="wordmark">
    <span class="wordmark__mark"></span>
    <span class="wordmark__name">HARCOURT</span>
    <span class="wordmark__sub">MEMORIALS</span>
  </div>
  <div class="front-band"></div>
</section>

<section class="card card--back" aria-label="Card back">
  <svg class="back-art" viewBox="0 0 481 291" preserveAspectRatio="none" aria-hidden="true">
    <defs>
      <radialGradient id="sheen" cx="0.78" cy="0.45" r="0.5">
        <stop offset="0" stop-color="#3a3a3a"/>
        <stop offset="1" stop-color="#0d0d0d"/>
      </radialGradient>
    </defs>
    <path d="M0 0 H316 C268 60 240 160 294 291 H0 Z" fill="url(#sheen)"/>
    <path d="M330 0 H348 C300 55 266 140 272 232 C254 150 272 60 330 0 Z" fill="var(--gold)"/>
  </svg>

  <div class="person">
    <div class="person__name">SIMON HARCOURT</div>
    <div class="person__role">Operations Manager</div>
  </div>

  <div class="contact">
    <p class="contact__address">Suite 17, 8 Palfrey Lane,<br>West Carlow, Sydney NSW 2156</p>
    <ul class="contact__list">
      <li class="contact__item">
        <svg class="contact__icon" viewBox="0 0 10 10"><path d="M2 0.5 L4 2.5 L3 4 Q4.5 6 6 7 L7.5 6 L9.5 8 L8 9.5 Q2 8 0.5 2 Z" fill="var(--gold)"/></svg>
        0417293086
      </li>
      <li class="contact__item">
        <svg class="contact__icon" viewBox="0 0 10 10"><path d="M0.5 3.5 Q5 0.5 9.5 3.5 L8 4.5 L7 3.5 H3 L2 4.5 Z M2 5 H8 L9 9.5 H1 Z" fill="var(--gold)"/></svg>
        02 9561 3048
      </li>
      <li class="contact__item">
        <svg class="contact__icon" viewBox="0 0 10 10"><rect x="0.5" y="2" width="9" height="6.5" fill="var(--gold)"/><path d="M0.5 2 L5 5.8 L9.5 2" stroke="#0d0d0d" stroke-width=".9" fill="none"/></svg>
        simon@harcourtmemorials.com.au
      </li>
      <li class="contact__item">
        <svg class="contact__icon" viewBox="0 0 10 10"><circle cx="5" cy="5" r="4.5" fill="var(--gold)"/><path d="M0.5 5 H9.5 M5 0.5 Q2 5 5 9.5 Q8 5 5 0.5" stroke="#0d0d0d" stroke-width=".7" fill="none"/></svg>
        www.harcourtmemorials.com.au
      </li>
    </ul>
  </div>

  <div class="wordmark">
    <span class="wordmark__mark"></span>
    <span class="wordmark__name">HARCOURT</span>
    <span class="wordmark__sub">MEMORIALS</span>
  </div>
</section>

</body>
</html>
```